Wine Shop Banners

Banner graphic/images required
Require banner images to match the present online wine shop.

www.korbel-tafelhaus.de

The wine-shop presently has a very clean, simple design, lots of white space, which is very much the trend at the moment.

Requirements
Images or graphic design for present banners visible on the homepage

The colour and feeling of the banners must fit in with the present clean, simple design.

Work required
3 large slide-card/banners (can be more) and 3 smaller fixed banners below. Please view website to see present position of banners.

LARGE BANNERS x 3

Something special with white background within the banner space
White background on each slide-card. Small individual graphic image in the middle of the slide card. This could be either a simple element of wine:
ingredients, fruit (grape), bottle, cork, old bottle label etc. just displaying one item on each slide-card. Preferably with high quality graphic features.

Note:
We are trying the steer away from the classic stereotype wineshop design. The image/s should have a higher, individual graphic touch, which gives the design something different. Sometimes such artistic work is displayed in steampunk or even in nostalgic design, which leaves the viewer slightly memorized with the content.
To clarify: we are not looking for a full steampunk design but possibly certain elements of this will give you an idea what we mean. That is to say, the design can go slightly in this direction without going over the top. Something small but very eye-catching.

SMALLER BANNERS x 3

One idea is:
Showing a symbol e.g. - discount sign "%" against a white background but again with a high graphic quality.

Target Market(s)

People interested in purchasing wine.
Ages approx. 25 to 65

Industry/Entity Type

Shop

Requirements
Must have
• Something special with white background
• Small individual graphic image in the middle of the slide card.
Nice to have
• The image/s should have a higher, individual graphic touch, which gives the design something different. Something that leaves the viewer slightly memorized with the content.
Should not have
• Not the typical classical design that is often seen on wine shops.

```html
<!DOCTYPE html>
<html lang="en">
<head>
<meta charset="utf-8">
<title>Wine Shop Banners</title>
<link rel="stylesheet" href="https://fonts.googleapis.com/css2?family=Bodoni+Moda:wght@400;500;600&display=swap">
<style>
  :root {
    --bg-top: #cdd1c7;
    --bg-bottom: #a2aa95;
    --card: #ffffff;
    --olive: #717a50;
    --olive-light: #8c9452;
    --wine: #a91f4a;
    --sketch: #e9ebe4;
    --vine-shadow: #7f8a70;
  }
  html, body {
    margin: 0;
    padding: 0;
    width: 886px;
    height: 1200px;
    overflow: hidden;
  }
  body {
    position: relative;
    background: linear-gradient(180deg, var(--bg-top) 0%, #b9beb1 50%, var(--bg-bottom) 100%);
    font-family: "Bodoni Moda", "Didot", serif;
  }
  .vine-decor {
    position: absolute;
    border-radius: 50%;
    opacity: 0.55;
  }
  .vine-decor--top {
    left: -60px; top: -40px; width: 310px; height: 330px;
    background: radial-gradient(circle at 40% 40%, var(--vine-shadow) 0%, rgba(127,138,112,0.4) 45%, rgba(127,138,112,0) 70%);
  }
  .vine-decor--bottom {
    right: -70px; bottom: -40px; width: 330px; height: 400px;
    background: radial-gradient(circle at 60% 55%, var(--vine-shadow) 0%, rgba(127,138,112,0.45) 45%, rgba(127,138,112,0) 70%);
  }
  .banner {
    position: absolute;
    left: 165px;
    width: 558px;
    height: 261px;
    background: var(--card);
    box-shadow: 0 26px 30px -14px rgba(60, 66, 52, 0.55);
    text-align: center;
    overflow: hidden;
  }
  .banner--shipping { top: 121px; }
  .banner--celebrate { top: 478px; }
  .banner--offer { top: 831px; }
  .landscape-sketch {
    position: absolute;
    left: 0; right: 0; bottom: 0; height: 55%;
    background: linear-gradient(180deg, rgba(233,235,228,0) 0%, var(--sketch) 100%);
  }
  .grape-border {
    position: absolute;
    left: 35px; right: 22px; top: 0; height: 74px;
    background: linear-gradient(180deg, #eeeeee 0%, #f7f7f7 100%);
  }
  .headline {
    position: absolute;
    left: 0; right: 0;
    margin: 0;
    color: var(--olive);
    font-weight: 500;
    font-size: 60px;
    line-height: 1;
    letter-spacing: 1px;
  }
  .subline {
    position: absolute;
    left: 0; right: 0;
    margin: 0;
    color: var(--olive-light);
    font-size: 20px;
    line-height: 1;
    letter-spacing: 0.6px;
  }
  .banner--shipping .headline { top: 66px; }
  .banner--shipping .subline { top: 130px; }
  .price {
    position: absolute;
    left: 0; right: 0; top: 162px;
    margin: 0;
    color: var(--wine);
    font-size: 54px;
    font-weight: 500;
    line-height: 1;
    letter-spacing: 2px;
  }
  .banner--celebrate .headline { top: 86px; font-size: 62px; }
  .banner--celebrate .subline { top: 153px; font-size: 20.5px; }
  .banner--offer .headline { top: 68px; font-size: 60px; }
  .discount {
    position: absolute;
    left: 0; top: 0;
    width: 100%; height: 100%;
    color: var(--wine);
    text-align: left;
  }
  .discount__number {
    position: absolute; left: 197px; top: 119px;
    font-size: 68px; font-weight: 500; line-height: 1;
    transform: scaleX(1.25);
    transform-origin: left top;
  }
  .discount__off {
    position: absolute; left: 197px; top: 180px;
    font-size: 46px; font-weight: 500; line-height: 1;
    letter-spacing: 1px;
  }
  .discount__sign {
    position: absolute; left: 309px; top: 112px;
    font-size: 116px; font-weight: 400; line-height: 1;
  }
</style>
</head>
<body>
  <div class="vine-decor vine-decor--top" role="img" aria-label="Engraved grape cluster decoration"></div>
  <div class="vine-decor vine-decor--bottom" role="img" aria-label="Engraved grape cluster decoration"></div>

  <section class="banner banner--shipping">
    <div class="landscape-sketch" role="img" aria-label="Faint engraved vineyard landscape"></div>
    <h2 class="headline">FREE SHIPPING</h2>
    <p class="subline">ON ORDERS OVER</p>
    <p class="price">$25</p>
  </section>

  <section class="banner banner--celebrate">
    <div class="landscape-sketch" role="img" aria-label="Faint engraved vineyard landscape"></div>
    <div class="grape-border" role="img" aria-label="Line drawing of hanging grape clusters"></div>
    <h2 class="headline">CELEBRATE</h2>
    <p class="subline">YOUR ANNIVERSARY WITH TASTE</p>
  </section>

  <section class="banner banner--offer">
    <div class="landscape-sketch" role="img" aria-label="Faint engraved vineyard landscape"></div>
    <h2 class="headline">SPECIAL OFFER</h2>
    <div class="discount">
      <span class="discount__number">20</span>
      <span class="discount__off">OFF</span>
      <span class="discount__sign">%</span>
    </div>
  </section>
</body>
</html>
```